Website Design for The Elder Nook

Please design and code a new website.
Here are the sites I like best:
http://www.voyaglint.com/alternate/
http://www.wheelgiftbay.org
Please make it similar but look at the competitor site (below) for images and wording. This is NOT a car donation site. It's a senior lead placement site like https://www.kinhavenfinder.com. I just like this sites above as a lead generation sites.
Competitor site:
https://www.kinhavenfinder.com (use ideas / verbiage from this site)
Updates
Competitor site:
Coding
Coded - Design and coding required
Number of Pages Required
1 page
Look and feel
Each slider illustrates characteristics of the customer's brand and the style your logo design should communicate.

```html
<!DOCTYPE html>
<html lang="en">
<head>
<meta charset="utf-8">
<title>The Elder Nook</title>
<link href="https://fonts.googleapis.com/css2?family=Prata&family=Nunito+Sans:wght@300;400;600&display=swap" rel="stylesheet">
<style>
:root{
  --blue:#0f5db4;
  --blue-dark:#0b4e9c;
  --green:#8cc63f;
  --ink:#333;
  --muted:#777;
  --line:#e2e2e2;
  --serif:'Prata', Georgia, serif;
  --sans:'Nunito Sans', Arial, sans-serif;
}
*{box-sizing:border-box;margin:0;padding:0}
html,body{width:1200px;height:3040px;overflow:hidden}
body{font-family:var(--sans);color:var(--ink);background:#fff}
.wrap{width:916px;margin:0 auto;position:relative}
.g{color:var(--green)}.b{color:var(--blue)}
.chev{display:inline-block;width:7px;height:5px;margin-left:3px;vertical-align:middle}

/* header */
.site-header{height:91px}
.site-header .wrap{display:flex;align-items:center;height:91px}
.brand{display:flex;align-items:center;gap:10px;font-family:var(--serif);font-size:22px;color:var(--blue)}
.brand-dot{width:26px;height:26px;border-radius:50%;background:var(--green)}
.call{margin-left:auto;display:flex;align-items:center;gap:10px}
.call small{display:block;font-family:var(--serif);font-size:11px;color:#444}
.call strong{font-size:24px;font-weight:400;color:#222}
.badge{width:126px;height:48px;background:var(--blue-dark);border-radius:4px;margin-left:26px}
.lang{margin-left:24px;width:102px;height:34px;border:1px solid var(--line);border-radius:3px;display:flex;align-items:center;gap:8px;padding-left:14px;font-size:13px;color:#555}
.lang span.flag{width:34px;height:18px;background:linear-gradient(#b22 0 50%,#eee 50%);border-radius:2px}

.main-nav{background:var(--blue);height:42px}
.main-nav ul{list-style:none;display:flex;height:42px;white-space:nowrap}
.main-nav li{font-family:var(--serif);font-size:11.5px;color:#fff;padding:0 10.5px;display:flex;align-items:center;border-right:1px solid rgba(255,255,255,.18)}
.main-nav li.active{background:var(--blue-dark);border-bottom:3px solid var(--green)}

/* hero */
.hero{height:510px;position:relative;background:linear-gradient(100deg,#b9b98a 0%,#d9d6b6 30%,#e9e4cf 45%,#c7a78a 65%,#a98a70 80%,#6e8a5b 100%)}
.inquiry{position:absolute;left:142px;top:46px;width:364px;height:418px;background:#fff;box-shadow:0 2px 10px rgba(0,0,0,.15)}
.inquiry h2{background:var(--green);color:#fff;font-family:var(--serif);font-weight:400;font-size:24px;text-align:center;height:62px;line-height:62px}
.inquiry form{padding:29px 29px 0}
.field{display:flex;border:1px solid #d6d6d6;border-radius:3px;height:42px;margin-bottom:12px}
.field i{width:40px;border-right:1px solid #d6d6d6;display:flex;align-items:center;justify-content:center}
.field span{padding:0 17px;font-size:13px;color:#666;line-height:40px}
.field.msg{height:70px}
.submit{display:block;width:100%;height:38px;background:var(--blue);color:#fff;border:0;border-radius:2px;font-family:var(--serif);font-size:15px;margin-top:8px}
.tagline{background:#000;height:63px;text-align:center;line-height:63px;font-family:var(--serif);color:#fff;font-size:24px}
.tagline em{color:var(--green)}

/* support */
.support{height:545px;padding-top:78px;text-align:center}
.sec-title{font-family:var(--serif);font-weight:400;font-size:29px}
.lead{font-size:14px;line-height:24px;color:#333;margin-top:14px}
.features{display:flex;gap:14px;margin-top:24px}
.feature{width:172px;height:181px;border:1px solid var(--line);box-shadow:0 2px 5px rgba(0,0,0,.07);padding-top:24px;font-size:17px;line-height:21px;color:#333;font-weight:300}
.feature svg{width:56px;height:56px;display:block;margin:0 auto 10px}
.no-cost{display:flex;align-items:center;margin-top:52px;text-align:left}
.no-cost h3{font-family:var(--serif);font-weight:400;font-size:24px;width:286px;white-space:nowrap}
.no-cost p{font-size:16px;line-height:25px;width:430px;color:#333;margin-left:-6px}
.no-cost .tel{margin-left:auto;color:var(--blue);font-size:21px}

/* advisor */
.advisor{height:480px;background:linear-gradient(90deg,#1b5aa8,#2a6fc0 30%,#2366b6 60%,#1b5aa8);color:#fff;text-align:center;padding-top:78px}
.advisor h2{font-family:var(--serif);font-weight:400;font-size:29px}
.advisor p.lead{color:#fff;margin-top:10px}
.perks{display:flex;justify-content:center;gap:62px;margin-top:18px}
.perk{width:198px;font-size:16px;line-height:20px;font-weight:300}
.perk .ring{width:96px;height:96px;border:1.5px solid #fff;border-radius:50%;margin:0 auto 14px;display:flex;align-items:center;justify-content:center}
.finder{width:604px;height:46px;margin:30px auto 0;background:#fff;border-radius:3px;display:flex;align-items:center;padding:4px}
.finder span{flex:1;text-align:left;color:#333;font-size:14px;padding-left:16px}
.finder b{width:222px;height:38px;background:var(--green);color:#fff;font-family:var(--serif);font-weight:400;font-size:15px;line-height:38px}

/* testimonials */
.reviews{height:484px;padding-top:74px;text-align:center}
.cards{display:flex;justify-content:space-between;margin-top:28px}
.card{width:285px;text-align:left}
.card blockquote{border:1px solid var(--line);height:148px;padding:14px 17px;font-size:12.5px;line-height:21.5px;color:#777;white-space:nowrap;overflow:hidden}
.who{display:flex;align-items:center;gap:18px;margin:-22px 0 0 9px;position:relative}
.avatar{width:70px;height:70px;border-radius:50%;border:3px solid var(--blue);background:radial-gradient(circle at 50% 40%,#e8cbb0,#9b7a5d)}
.who b{font-family:var(--serif);font-weight:400;font-size:14px;color:#333;margin-top:18px}
.btn-green{display:inline-block;background:var(--green);color:#fff;font-family:var(--serif);font-size:15px;padding:0 24px;height:38px;line-height:38px;border-radius:2px}
.reviews .btn-green{margin-top:30px;width:208px;padding:0}

/* veterans */
.veterans{height:291px;background:linear-gradient(160deg,#2a2d3a 0%,#545763 30%,#3a3232 55%,#5a2424 75%,#1d1d22 100%);color:#fff;text-align:center;padding-top:62px}
.veterans h2{font-family:var(--serif);font-weight:400;font-size:25px}
.veterans p{font-size:14px;line-height:24px;margin-top:10px}
.veterans .btn-green{margin-top:16px;width:130px;padding:0}

/* states */
.states{height:365px;padding-top:86px;text-align:center}
.state-cols{display:flex;text-align:left;margin:20px 0 0 18px}
.state-cols ul{list-style:none;font-size:13px;line-height:21.8px;color:#444}
.state-cols li::before{content:"› "}

/* footer */
.site-footer{height:169px;background:var(--blue);color:#fff;padding-top:51px}
.foot-nav{display:flex;justify-content:center;gap:34px;font-family:var(--serif);font-size:11px;list-style:none;white-space:nowrap}
.foot-bottom{border-top:1px solid rgba(255,255,255,.25);margin-top:40px;padding-top:14px;display:flex;align-items:center;font-size:13px}
.social{margin-left:auto;display:flex;gap:6px}
.social i{width:24px;height:24px;border-radius:50%;border:1.5px solid #fff;display:block}
</style>
</head>
<body>

<header class="site-header">
  <div class="wrap">
    <div class="brand"><span class="brand-dot"></span>The Elder Nook</div>
    <div class="call">
      <svg width="34" height="34" viewBox="0 0 24 24" fill="none" stroke="#0f5db4" stroke-width="1.4"><path d="M5 3h4l2 5-2.5 1.5a11 11 0 0 0 6 6L16 13l5 2v4a2 2 0 0 1-2 2A16 16 0 0 1 3 5a2 2 0 0 1 2-2z"/></svg>
      <div><small>Talk to a local advisor for FREE</small><strong>(123) 456-7890</strong></div>
    </div>
    <div class="badge" role="img" aria-label="Accreditation badge"></div>
    <div class="lang">EN : <span class="flag" role="img" aria-label="Language flag"></span></div>
  </div>
</header>

<nav class="main-nav">
  <div class="wrap">
    <ul>
      <li class="active">ASSISTED LIVING</li>
      <li>MEMORY CARE</li>
      <li>NURSING HOMES</li>
      <li>MORE LIVING OPTIONS<svg class="chev" viewBox="0 0 7 5" fill="none" stroke="#fff" stroke-width="1.2"><path d="M.5.5 3.5 4 6.5.5"/></svg></li>
      <li>PLANNING &amp; ADVICE</li>
      <li>HOW OUR SERVICE WORKS</li>
    </ul>
  </div>
</nav>

<section class="hero" role="img" aria-label="Smiling senior couple embracing outdoors in a sunny park">
  <div class="inquiry">
    <h2>Quick Inquiry</h2>
    <form>
      <div class="field"><i><svg width="12" height="12" viewBox="0 0 12 12" fill="#444"><circle cx="6" cy="3.5" r="2.5"/><path d="M1 12a5 5 0 0 1 10 0z"/></svg></i><span>Name</span></div>
      <div class="field"><i><svg width="12" height="12" viewBox="0 0 24 24" fill="#444"><path d="M5 3h4l2 5-2.5 1.5a11 11 0 0 0 6 6L16 13l5 2v4a2 2 0 0 1-2 2A16 16 0 0 1 3 5a2 2 0 0 1 2-2z"/></svg></i><span>Phone</span></div>
      <div class="field"><i><svg width="12" height="10" viewBox="0 0 12 10" fill="#444"><path d="M0 0h12v1.5L6 5 0 1.5zM0 3l6 3.5L12 3v7H0z"/></svg></i><span>Email</span></div>
      <div class="field msg"><i style="align-items:flex-start;padding-top:14px"><svg width="13" height="11" viewBox="0 0 13 11" fill="#444"><ellipse cx="5" cy="4" rx="5" ry="3.5"/><ellipse cx="8.5" cy="7" rx="4.5" ry="3"/></svg></i><span>Message</span></div>
      <button class="submit" type="button">Submit Now</button>
    </form>
  </div>
</section>

<div class="tagline">You know your family.We know <em>Senior Living.</em></div>

<section class="support">
  <div class="wrap">
    <h2 class="sec-title"><span class="g">The Support You Need To</span> <span class="b">Make The Right Choice</span></h2>
    <p class="lead">Lorem ipsum dolor sit amet, consectetuer adipiscing elit, sed diam nonummy nibh euismod tincidunt ut laoreet dolore magna<br>aliquam erat volutpat. Ut wisi enim ad minim veniam, quis nostrud exerci tation ullamcorper suscipit.</p>
    <div class="features">
      <div class="feature"><svg viewBox="0 0 56 56" fill="none" stroke="#8cc63f" stroke-width="2"><circle cx="28" cy="14" r="8"/><path d="M12 54V38a10 10 0 0 1 10-10h12a10 10 0 0 1 10 10v16M28 28v26"/></svg>Dedicated local<br>advisor</div>
      <div class="feature"><svg viewBox="0 0 56 56" fill="none" stroke="#8cc63f" stroke-width="2"><path d="M4 28 28 6l24 22M10 24v30h36V24"/><rect x="22" y="38" width="12" height="16"/><rect x="23" y="20" width="10" height="8"/></svg>Hand-picked list of<br>communities to<br>match your needs</div>
      <div class="feature"><svg viewBox="0 0 56 56" fill="none" stroke="#8cc63f" stroke-width="2"><circle cx="30" cy="20" r="10"/><path d="M30 14v12M27 17h5M27 23h5M4 44h10l10 4h14l14-10-4-3-12 6H26M14 40h12a3 3 0 0 1 0 6"/><path d="M30 2v4M22 4l2 3M38 4l-2 3"/></svg>Full details and<br>pricing</div>
      <div class="feature"><svg viewBox="0 0 56 56" fill="none" stroke="#8cc63f" stroke-width="2"><rect x="4" y="8" width="48" height="44"/><path d="M4 18h48M14 2v10M42 2v10M12 26h32v18H12zM12 35h32M20 26v18M28 26v18M36 26v18"/></svg>Help scheduling<br>tours</div>
      <div class="feature"><svg viewBox="0 0 56 56" fill="none" stroke="#8cc63f" stroke-width="2"><path d="M8 10h28v30H8M36 20h10l8 10v10h-4M2 18h12M4 26h10"/><circle cx="16" cy="44" r="5"/><circle cx="44" cy="44" r="5"/></svg>Move in<br>support</div>
    </div>
    <div class="no-cost">
      <h3><span class="g">There's</span> <span class="b">No Cost To You.</span></h3>
      <p>We work with over 20,000 senior living communities.<br>Our community partners pay us for placement services.</p>
      <span class="tel">Call (123) 456-7890</span>
    </div>
  </div>
</section>

<section class="advisor" role="img" aria-label="Blue-tinted portraits of friendly local advisors">
  <h2>Your local advisor informs. You decide.</h2>
  <p class="lead">Lorem ipsum dolor sit amet, consectetuer adipiscing elit, sed diam nonummy nibh euismod tincidunt ut laoreet.</p>
  <div class="perks">
    <div class="perk"><div class="ring"><svg width="40" height="60" viewBox="0 0 40 60" fill="none" stroke="#fff" stroke-width="2"><circle cx="20" cy="14" r="11"/><path d="M20 25v32"/></svg></div>Insider's tips for the area<br>near you</div>
    <div class="perk"><div class="ring"><svg width="52" height="46" viewBox="0 0 52 46" fill="none" stroke="#fff" stroke-width="2.4"><path d="M26 43 5 22A12 12 0 0 1 26 8a12 12 0 0 1 21 14z"/></svg></div>Advice tailored to your<br>unique situation</div>
    <div class="perk"><div class="ring"><svg width="52" height="42" viewBox="0 0 52 42" fill="none" stroke="#fff" stroke-width="2"><circle cx="5" cy="5" r="4"/><circle cx="5" cy="21" r="4"/><circle cx="5" cy="37" r="4"/><path d="M16 5h34M16 21h34M16 37h34"/></svg></div>Time saving know-how and<br>resources</div>
  </div>
  <div class="finder"><span>Enter city or postal code</span><b>Find an advisor near you</b></div>
</section>

<section class="reviews">
  <div class="wrap">
    <h2 class="sec-title"><span class="g">93% Of Our Customers</span> <span class="b">Recommend Our Service</span></h2>
    <div class="cards">
      <div class="card"><blockquote>Lorem ipsum dolor sit amet, consectetuer<br>adipiscing elit, sed diam nonummy nibh<br>euismod tincidunt ut laoreet dolore magna<br>aliquam erat volutpat. Ut wisi enim ad<br>minim veniam, quis nostrud.</blockquote><div class="who"><div class="avatar" role="img" aria-label="Customer portrait"></div><b>Dana Hollis</b></div></div>
      <div class="card"><blockquote>Lorem ipsum dolor sit amet, consectetuer<br>adipiscing elit, sed diam nonummy nibh<br>euismod tincidunt ut laoreet dolore magna<br>aliquam erat volutpat. Ut wisi enim ad<br>minim veniam, quis nostrud.</blockquote><div class="who"><div class="avatar" role="img" aria-label="Customer portrait"></div><b>Marc Devlin</b></div></div>
      <div class="card"><blockquote>Lorem ipsum dolor sit amet, consectetuer<br>adipiscing elit, sed diam nonummy nibh<br>euismod tincidunt ut laoreet dolore magna<br>aliquam erat volutpat. Ut wisi enim ad<br>minim veniam, quis nostrud.</blockquote><div class="who"><div class="avatar" role="img" aria-label="Customer portrait"></div><b>Tessa Bright</b></div></div>
    </div>
    <span class="btn-green">See More Testimonials</span>
  </div>
</section>

<section class="veterans" role="img" aria-label="Waving national flag in dark tones">
  <h2>Access Up To $2,000 Per Month In Veteran's Aid</h2>
  <p>We work with Veterans every day. Most veteran families do not know of a key benefit available to them and their families.<br>It's called the Veteran's Aid and Attendance benefit. This benefit can help pay for senior living and home care.</p>
  <span class="btn-green">Learn More</span>
</section>

<section class="states">
  <div class="wrap">
    <h2 class="sec-title"><span class="g">Senior Assisted</span> <span class="b">Living by State</span></h2>
    <div class="state-cols">
      <ul style="width:142px"><li>Alabama</li><li>Arizona</li><li>Arkansas</li><li>California</li><li>Colorado</li><li>Connecticut</li><li>Delaware</li></ul>
      <ul style="width:185px"><li>District of Columbia</li><li>Florida</li><li>Georgia</li><li>Hawaii</li><li>Idaho</li><li>Illinois</li><li>Indiana</li></ul>
      <ul style="width:158px"><li>Iowa</li><li>Kansas</li><li>Kentucky</li><li>Louisiana</li><li>Maine</li><li>Maryland</li><li>Massachusetts</li></ul>
      <ul style="width:136px"><li>Michigan</li><li>Minnesota</li><li>Mississippi</li><li>Missouri</li><li>Montana</li><li>Nebraska</li><li>Nevada</li></ul>
      <ul style="width:169px"><li>New Hampshire</li><li>New Jersey</li><li>New Mexico</li><li>New York</li><li>North Carolina</li><li>North Dakota</li><li>Ohio</li></ul>
      <ul><li>Oklahoma</li><li>Oregon</li><li>Pennsylvania</li><li>Rhode Island</li><li>South Carolina</li><li>South Dakota</li><li>Tennessee</li></ul>
    </div>
  </div>
</section>

<footer class="site-footer">
  <div class="wrap">
    <ul class="foot-nav">
      <li>ASSISTED LIVING</li><li>MEMORY CARE</li><li>NURSING HOMES</li><li>MORE LIVING OPTIONS<svg class="chev" viewBox="0 0 7 5" fill="none" stroke="#fff" stroke-width="1.2"><path d="M.5.5 3.5 4 6.5.5"/></svg></li><li>PLANNING &amp; ADVICE</li><li>HOW OUR SERVICE WORKS</li>
    </ul>
    <div class="foot-bottom">
      <span>Copyright 2019 The Elder Nook. All Rights Reserved.</span>
      <div class="social"><i></i><i></i><i></i><i></i></div>
    </div>
  </div>
</footer>

</body>
</html>
```